PlayTallyCollective - Game Statistics and Achievement Tracking

I need a new modern design for an existing website.

The website is a project to track statistics and achievements for games (currently Vaporn Achievements/Stats and stats for Cargo Haul Odyssey 2 and Frontier Rig Journeys).
I am currently expanding the site with other platforms (like QVR) and more games.
I am also adding a user registration/signin with user profiles to show off their achievements and stats across all platforms and games.

The current website is available at https://plytly.example/
To search for data you can use the username "pixelornin" (without quotes).

The design should be modern and extendable and contain space for a logo.

The logo should match the project. It should combine Gaming with statistics.

Target Market(s)

Video game players

Number of Pages Required

5+ page

Font styles to use
Sans Serif

Requirements
Must have
• Basic Layout, User profile page (not yet available on live site), Search Page for Platforms/Games, Platform profile page, Dark theme

```html
<!DOCTYPE html>
<html lang="en">
<head>
<meta charset="utf-8">
<title>PlayTallyCollective – Game Statistics</title>
<link href="https://fonts.googleapis.com/css2?family=Montserrat:wght@400;500;600;700&display=swap" rel="stylesheet">
<style>
:root{
  --navy:#0b0e2c;
  --navy-deep:#070a22;
  --purple:#9a16e0;
  --purple-dark:#3c0b66;
  --violet:#5a1a9e;
  --white:#ffffff;
  --muted:#d6d3e6;
  --gold:#f2a81d;
  --cyan:#19e3e0;
}
*{margin:0;padding:0;box-sizing:border-box}
html,body{width:1200px;height:3562px;overflow:hidden}
body{background:var(--navy);font-family:'Montserrat',sans-serif;color:var(--white);position:relative}
.abs{position:absolute}
.btn{position:absolute;display:flex;align-items:center;justify-content:center;background:var(--purple);color:var(--white);border-radius:30px;font-weight:600;text-transform:uppercase}

/* hero */
.hero{left:0;top:0;width:1200px;height:557px;background:linear-gradient(180deg,#22135c 0%,#3a1282 35%,#5a17a8 62%,#2b2fd4 88%,#3a3cf0 100%)}
.hero-grid{left:0;top:300px;width:1200px;height:257px;background:linear-gradient(180deg,rgba(190,60,255,0.15),rgba(70,80,255,0.55))}
.logo{left:144px;top:44px;display:flex;align-items:center;gap:12px;font-weight:700;font-size:25px;color:var(--white)}
.logo-mark{width:46px;height:46px;border:3px solid var(--white);border-radius:6px}
.nav{left:568px;top:47px;display:flex;gap:0;font-size:14px;font-weight:500}
.nav a{position:absolute;color:var(--white);text-decoration:none;white-space:nowrap}
.nav a.active::after{content:"";position:absolute;left:0;right:0;bottom:-9px;height:2px;background:#ff6a3c}
.search-top{left:943px;top:37px;width:112px;height:36px;border:1px solid rgba(255,255,255,.6);border-radius:18px;font-size:11px;padding:11px 0 0 18px}
.hero-title{left:0;top:178px;width:1200px;text-align:center;font-size:40px;font-weight:500;line-height:51px}

/* profile */
.profile{left:145px;top:424px;width:910px;height:305px;border-radius:153px;background:linear-gradient(180deg,#4a0c7a,#360a60);box-shadow:0 10px 40px rgba(0,0,0,.4)}
.avatar-ring{left:180px;top:457px;width:238px;height:238px;border-radius:50%;background:#141c33}
.avatar{left:227px;top:506px;width:144px;height:142px;border-radius:6px;background:linear-gradient(160deg,#3fa6e8,#1d5ea8);box-shadow:0 0 12px #2bd0ff}
.p-name{left:478px;top:480px;font-size:21px;font-weight:500}
.p-rows{left:478px;top:532px;font-size:13.5px;line-height:24px}
.p-rows div{position:relative;height:24px}
.p-rows span{position:absolute;left:139px;white-space:nowrap}
.side-icon{width:32px;height:32px;border-radius:50%;border:1.5px solid #fff;background:#12102a}
.badge{width:26px;height:26px;border-radius:50%;border:1.5px solid #b8a24a;font-size:10px;display:flex;align-items:center;justify-content:center}

/* history */
.history{left:0;top:729px;width:1200px;height:504px;background:radial-gradient(ellipse at 50% 60%,#1a2a55 0%,#0d1430 55%,#080b22 100%)}
.h2{position:absolute;width:1200px;left:0;text-align:center;font-size:38px;font-weight:500}
.history-text{left:194px;top:880px;width:812px;font-size:15px;line-height:24px;text-align:justify;text-align-last:center;color:var(--white)}

/* games */
.games{left:0;top:1233px;width:1200px;height:960px;background:radial-gradient(ellipse at 0% 30%,#4a1577 0%,rgba(11,14,44,0) 35%),var(--navy)}
.games-title{left:149px;top:1323px;font-size:37px;font-weight:500}
.games-search{left:546px;top:1324px;width:509px;height:42px;border:1px solid rgba(255,255,255,.55);border-radius:21px;font-size:12px;padding:13px 0 0 27px}
.games-search i{position:absolute;right:8px;top:8px;width:25px;height:25px;border-radius:50%;background:var(--purple)}
.thumb{position:absolute;width:283px;height:218px;border-radius:14px}
.card-title{position:absolute;font-size:13.5px;font-weight:500;text-transform:uppercase}
.card-time{position:absolute;font-size:12px;display:flex;align-items:center;gap:8px}
.card-btn{width:117px;height:32px;font-size:12.5px}
.arrow{position:absolute;width:44px;height:44px;border-radius:50%;border:1.5px solid rgba(255,255,255,.7)}

/* vaporn */
.cubes{left:0;top:2180px;width:1200px;height:250px;background:linear-gradient(180deg,rgba(11,14,44,0),rgba(150,20,60,.45) 40%,rgba(60,20,90,.35) 70%,rgba(11,14,44,0))}
.stat{position:absolute;width:180px;text-align:center}
.stat-num{font-size:22px;font-weight:700}
.stat-label{font-size:13px;line-height:16px}
.contact{left:0;top:2878px;width:1200px;height:541px;background:radial-gradient(ellipse at 50% 100%,#3a1f6a 0%,#191446 45%,#0d0f33 100%)}
.field{position:absolute;font-size:13px;border-bottom:1px solid rgba(255,255,255,.7);padding-bottom:14px}
.footer{left:0;top:3419px;width:1200px;height:143px;background:var(--navy-deep)}
.social{position:absolute;width:28px;height:28px;border-radius:50%;background:#fff}
</style>
</head>
<body>

<!-- hero -->
<div class="abs hero"></div>
<div class="abs hero-grid" role="img" aria-label="Neon perspective grid landscape"></div>
<div class="abs logo"><span class="logo-mark"></span>PlayTallyCollective</div>
<nav class="abs nav">
  <a class="active" style="left:0">HOME</a>
  <a style="left:78px">ABOUT US</a>
  <a style="left:183px">GAMES</a>
  <a style="left:267px">ABOUT US</a>
</nav>
<div class="abs search-top">Search
  <svg class="abs" style="right:12px;top:12px" width="11" height="11" viewBox="0 0 12 12"><circle cx="5" cy="5" r="3.8" fill="none" stroke="#fff" stroke-width="1.8"/><line x1="8" y1="8" x2="11" y2="11" stroke="#fff" stroke-width="1.8"/></svg>
</div>
<h1 class="abs hero-title">TRACKING EVERY PLAY,<br>POWERING EVERY GAME</h1>
<div class="btn" style="left:518px;top:319px;width:164px;height:47px;font-size:15px">Get Started</div>

<!-- scroll hint -->
<svg class="abs" style="left:1119px;top:452px" width="26" height="62" viewBox="0 0 26 62">
  <rect x="1" y="1" width="24" height="42" rx="12" fill="#fff"/>
  <rect x="11" y="7" width="4" height="8" rx="2" fill="#0b0e2c"/>
  <path d="M13 48v10M9 54l4 4 4-4" stroke="#8a7dff" stroke-width="1.5" fill="none"/>
</svg>

<!-- profile card -->
<div class="abs profile"></div>
<div class="abs avatar-ring"></div>
<div class="abs avatar" role="img" aria-label="Player avatar artwork"></div>
<div class="abs p-name">PIXELORNIN</div>
<div class="abs p-rows">
  <div>Played Games<span>: 1166 / 1644 (70%)</span></div>
  <div>Total play time<span>:1 year 2 months 11 hours 25 minutes</span></div>
  <div>Achievements<span>: 18007 / 63070 (28%)</span></div>
  <div>Member since<span>:14.01.2009</span></div>
  <div>Last played<span>&nbsp;&nbsp;: Rail Conductor 5</span></div>
  <div>Last Update<span>:26.12.2024 16:00h</span></div>
</div>
<svg class="abs" style="left:934px;top:464px" width="32" height="32" viewBox="0 0 32 32"><circle cx="16" cy="16" r="16" fill="var(--gold)"/><path d="M22 16a6 6 0 1 1-2-4.5" stroke="#fff" stroke-width="2.2" fill="none"/><path d="M20 8v4h4" stroke="#fff" stroke-width="2.2" fill="none"/></svg>
<div class="abs side-icon" style="left:934px;top:507px"><svg width="29" height="29" viewBox="0 0 29 29"><rect x="8" y="9" width="13" height="12" rx="2" stroke="#fff" stroke-width="1.5" fill="none"/><line x1="8" y1="13" x2="21" y2="13" stroke="#fff" stroke-width="1.5"/></svg></div>
<div class="abs side-icon" style="left:934px;top:549px"><svg width="29" height="29" viewBox="0 0 29 29"><circle cx="14.5" cy="14.5" r="7" fill="#fff"/></svg></div>
<div class="abs side-icon" style="left:934px;top:592px"><svg width="29" height="29" viewBox="0 0 29 29"><ellipse cx="14.5" cy="9" rx="5" ry="2" stroke="#fff" stroke-width="1.5" fill="none"/><path d="M9.5 9v10c0 1 2 2 5 2s5-1 5-2V9M9.5 14c0 1 2 2 5 2s5-1 5-2" stroke="#fff" stroke-width="1.5" fill="none"/></svg></div>
<div class="abs badge" style="left:815px;top:645px">179</div>
<div class="abs badge" style="left:854px;top:645px">15</div>
<div class="abs badge" style="left:894px;top:645px">87</div>
<svg class="abs" style="left:934px;top:646px" width="32" height="24" viewBox="0 0 32 24"><rect width="32" height="8" fill="#000"/><rect y="8" width="32" height="8" fill="#dd0000"/><rect y="16" width="32" height="8" fill="#ffce00"/></svg>

<!-- history -->
<div class="abs history" role="img" aria-label="Futuristic sci-fi corridor with glowing lights"></div>
<h2 class="h2" style="top:806px">OUR HISTORY</h2>
<p class="abs history-text">The PlayTallyCollective, short PTally or P-Tally, was established in August 2012 as a website providing game statistics for the Syndicate 2 Multiplayer Modification, that was work in progress back in the date and has sadly been canceled some years later, and Blockcraft with a custom Brickit plugin.After the Syndicate 2 Multiplayer Modification had been cancelled and Brickit has been shutdown the network moved on to provide game time and achievement statistics for Vaporn.Years later, in the year 2020, the service has been rewritten in it's core using modern cloud-native technology and started to expand statistics beyond Vaporn.</p>
<div class="btn" style="left:518px;top:1060px;width:164px;height:47px;font-size:15px">Read More</div>

<!-- games -->
<div class="abs games"></div>
<h2 class="abs games-title">OUR GAMES</h2>
<div class="abs games-search">Search for games..<i><svg width="25" height="25" viewBox="0 0 25 25"><circle cx="11.5" cy="11.5" r="4" fill="none" stroke="#fff" stroke-width="2"/><line x1="14.5" y1="14.5" x2="17.5" y2="17.5" stroke="#fff" stroke-width="2"/></svg></i></div>

<div class="thumb" style="left:147px;top:1425px;background:linear-gradient(135deg,#c45a1c,#3a5a1a 60%,#1e2a12)" role="img" aria-label="Ledger Quest+ game artwork"></div>
<div class="abs" style="left:452px;top:1419px;width:295px;height:230px;border-radius:18px;border:3px solid #2e2f48"></div>
<div class="thumb" style="left:458px;top:1425px;background:radial-gradient(circle at 50% 50%,#5a0a0a,#0c0c0c 70%)" role="img" aria-label="Vacant Hall game artwork"></div>
<svg class="abs" style="left:584px;top:1517px" width="32" height="32" viewBox="0 0 32 32"><circle cx="16" cy="16" r="16" fill="#f08a1c"/><path d="M16 10v12M10 16h12" stroke="#fff" stroke-width="2"/></svg>
<div class="thumb" style="left:767px;top:1425px;background:linear-gradient(160deg,#3d3fa0,#7a3fbf 55%,#2f2a70)" role="img" aria-label="Logicweave game artwork"></div>

<div class="card-title" style="left:151px;top:1682px">Ledger Quest+</div>
<div class="card-title" style="left:461px;top:1682px">Toward The Orbit</div>
<div class="card-title" style="left:769px;top:1682px">Logicweave</div>
<div class="btn card-btn" style="left:310px;top:1684px">Read More</div>
<div class="btn card-btn" style="left:621px;top:1684px">Read More</div>
<div class="btn card-btn" style="left:930px;top:1684px">Read More</div>

<div class="thumb" style="left:147px;top:1778px;background:linear-gradient(160deg,#5a1010,#1a1a2e 60%,#3a0a18)" role="img" aria-label="Breakout2091 game artwork"></div>
<div class="thumb" style="left:458px;top:1778px;background:linear-gradient(180deg,#8a5a2a,#c47a22 55%,#5a3a1a)" role="img" aria-label="Riddle Vaults game artwork"></div>
<div class="thumb" style="left:767px;top:1778px;background:linear-gradient(160deg,#6fc0e8,#b8e0f0 50%,#f0b0d8)" role="img" aria-label="Squashlings game artwork"></div>

<div class="card-title" style="left:150px;top:2034px">Breakout2091</div>
<div class="card-title" style="left:459px;top:2034px">Riddle Vaults</div>
<div class="card-title" style="left:770px;top:2034px">Squashlings</div>
<div class="btn card-btn" style="left:310px;top:2036px">Read More</div>
<div class="btn card-btn" style="left:621px;top:2036px">Read More</div>
<div class="btn card-btn" style="left:930px;top:2036px">Read More</div>

<div class="card-time" style="left:150px;top:1709px"><svg width="13" height="13" viewBox="0 0 13 13"><circle cx="6.5" cy="6.5" r="5.5" stroke="#fff" stroke-width="1.4" fill="none"/><path d="M6.5 3.5v3l2 1.5" stroke="#fff" stroke-width="1.4" fill="none"/></svg>1 hour 28 minutes</div>
<div class="card-time" style="left:460px;top:1709px"><svg width="13" height="13" viewBox="0 0 13 13"><circle cx="6.5" cy="6.5" r="5.5" stroke="#fff" stroke-width="1.4" fill="none"/><path d="M6.5 3.5v3l2 1.5" stroke="#fff" stroke-width="1.4" fill="none"/></svg>1 hour 28 minutes</div>
<div class="card-time" style="left:770px;top:1709px"><svg width="13" height="13" viewBox="0 0 13 13"><circle cx="6.5" cy="6.5" r="5.5" stroke="#fff" stroke-width="1.4" fill="none"/><path d="M6.5 3.5v3l2 1.5" stroke="#fff" stroke-width="1.4" fill="none"/></svg>1 hour 28 minutes</div>
<div class="card-time" style="left:150px;top:2061px"><svg width="13" height="13" viewBox="0 0 13 13"><circle cx="6.5" cy="6.5" r="5.5" stroke="#fff" stroke-width="1.4" fill="none"/><path d="M6.5 3.5v3l2 1.5" stroke="#fff" stroke-width="1.4" fill="none"/></svg>1 hour 28 minutes</div>
<div class="card-time" style="left:460px;top:2061px"><svg width="13" height="13" viewBox="0 0 13 13"><circle cx="6.5" cy="6.5" r="5.5" stroke="#fff" stroke-width="1.4" fill="none"/><path d="M6.5 3.5v3l2 1.5" stroke="#fff" stroke-width="1.4" fill="none"/></svg>1 hour 28 minutes</div>
<div class="card-time" style="left:770px;top:2061px"><svg width="13" height="13" viewBox="0 0 13 13"><circle cx="6.5" cy="6.5" r="5.5" stroke="#fff" stroke-width="1.4" fill="none"/><path d="M6.5 3.5v3l2 1.5" stroke="#fff" stroke-width="1.4" fill="none"/></svg>1 hour 28 minutes</div>

<div class="arrow" style="left:550px;top:2149px"><svg width="41" height="41" viewBox="0 0 41 41"><path d="M23 13l-7 7.5 7 7.5" stroke="#fff" stroke-width="2" fill="none"/></svg></div>
<div class="arrow" style="left:606px;top:2149px"><svg width="41" height="41" viewBox="0 0 41 41"><path d="M18 13l7 7.5-7 7.5" stroke="#fff" stroke-width="2" fill="none"/></svg></div>

<!-- vaporn stats -->
<div class="abs cubes" role="img" aria-label="Glowing red neon cubes floating in darkness"></div>
<h2 class="h2" style="top:2450px">OUR VAPORN</h2>

<svg class="abs" style="left:150px;top:2545px" width="960" height="186" viewBox="0 0 960 186">
  <g fill="none" stroke="rgba(255,255,255,.75)" stroke-width="1.5">
    <path d="M93 7a84 84 0 1 1-68 30"/>
    <path d="M328 7a84 84 0 1 1-68 30"/>
    <path d="M580 7a84 84 0 1 1-68 30"/>
    <path d="M814 7a84 84 0 1 1-68 30"/>
  </g>
  <g fill="var(--navy)" stroke="rgba(255,255,255,.75)" stroke-width="1.5">
    <circle cx="119" cy="11" r="5"/><circle cx="361" cy="11" r="5"/><circle cx="603" cy="11" r="5"/><circle cx="846" cy="11" r="5"/>
  </g>
  <circle cx="580" cy="95" r="67" fill="var(--purple)"/>
</svg>

<svg class="abs" style="left:217px;top:2586px" width="40" height="26" viewBox="0 0 40 26"><rect x="1" y="1" width="38" height="24" rx="12" fill="var(--cyan)"/><path d="M10 13h8M14 9v8" stroke="#0b0e2c" stroke-width="2.5"/><circle cx="27" cy="11" r="2" fill="#0b0e2c"/><circle cx="31" cy="15" r="2" fill="#0b0e2c"/></svg>
<div class="stat" style="left:147px;top:2627px"><div class="stat-num">251966</div><div class="stat-label" style="margin-top:6px">Games</div></div>

<svg class="abs" style="left:463px;top:2580px" width="32" height="40" viewBox="0 0 32 40"><path d="M9 24l-3 15 10-5 10 5-3-15" fill="var(--gold)"/><circle cx="16" cy="14" r="13" fill="var(--gold)"/><circle cx="16" cy="14" r="6" fill="#0b0e2c"/></svg>
<div class="stat" style="left:388px;top:2627px"><div class="stat-num">2692707</div><div class="stat-label">Game<br>Achievements</div></div>

<svg class="abs" style="left:710px;top:2582px" width="40" height="36" viewBox="0 0 40 36"><path d="M3 3v30h34" stroke="#fff" stroke-width="3.5" fill="none"/><path d="M9 25l9-10 6 6 11-13" stroke="#fff" stroke-width="3.5" fill="none"/></svg>
<div class="stat" style="left:640px;top:2629px"><div class="stat-num" style="font-size:20px">339284</div><div class="stat-label" style="margin-top:6px;font-size:12px">Game Stats</div></div>

<svg class="abs" style="left:942px;top:2580px" width="42" height="42" viewBox="0 0 42 42"><circle cx="21" cy="21" r="21" fill="var(--cyan)"/><path d="M21 10v12h8" stroke="#0b0e2c" stroke-width="3" fill="none"/></svg>
<div class="stat" style="left:874px;top:2627px"><div class="stat-num">3271530</div><div class="stat-label" style="margin-top:4px">Playtime<br>Records</div></div>

<div class="arrow" style="left:550px;top:2771px"><svg width="41" height="41" viewBox="0 0 41 41"><path d="M23 13l-7 7.5 7 7.5" stroke="#fff" stroke-width="2" fill="none"/></svg></div>
<div class="arrow" style="left:606px;top:2771px"><svg width="41" height="41" viewBox="0 0 41 41"><path d="M18 13l7 7.5-7 7.5" stroke="#fff" stroke-width="2" fill="none"/></svg></div>

<!-- contact -->
<div class="abs contact" role="img" aria-label="Night city skyline with glowing lights"></div>
<h2 class="h2" style="top:2956px">CONTACT US</h2>
<div class="field" style="left:358px;top:3049px;width:227px">Enter Name</div>
<div class="field" style="left:614px;top:3049px;width:227px">Enter Email</div>
<div class="field" style="left:358px;top:3122px;width:227px">Enter Phone</div>
<div class="field" style="left:614px;top:3122px;width:227px">Address</div>
<div class="field" style="left:358px;top:3194px;width:483px;padding-bottom:50px">Message</div>
<div class="btn" style="left:535px;top:3285px;width:130px;height:47px;font-size:15px">Submit</div>

<!-- footer -->
<footer class="abs footer"></footer>
<div class="abs" style="left:144px;top:3484px;font-size:13px">© 2024 PlayTallyCollective.All Rights Reserved &nbsp;|&nbsp; Privacy Policy &nbsp;|&nbsp; Terms of Use</div>
<div class="social" style="left:952px;top:3480px;background:var(--purple)"></div>
<div class="social" style="left:988px;top:3480px"></div>
<div class="social" style="left:1026px;top:3480px"></div>

</body>
</html>
```